Meadowrun Acres Website Design

We have been redeveloping our website already and are quite happy with the content, but the design needs to be better:
https://tilvexa-hub.examplehost.net/

Pages, content, concept etc. Can all be taken from the redeveloped website.
The farmer can register and edit/view their profile, subscribe and these pages need to be designed better as well as contact, about, pricing, tos, privacy and a page with example portlets.

We need a website to appeal to farmers, investors and retiring farmers.

The design should be clean and a little country.

We don't want any repeat designs that some may submit to every project and has no respect for the project brief, so please don't submit them.

Target Market(s)

farmers, investors, retirees

Industry/Entity Type

Farming

Number of Pages Required

5+ page

Colors

Designer to choose colors to be used in the design.

Requirements
Must have
• Nice, clean modern design that is appealing
• Profile page laid out nicely

```html
<!DOCTYPE html>
<html lang="en">
<head>
<meta charset="utf-8">
<title>Meadowrun Acres</title>
<link href="https://fonts.googleapis.com/css2?family=Raleway:wght@400;500;600;700&family=Open+Sans:ital,wght@0,400;0,600;1,400&display=swap" rel="stylesheet">
<style>
:root{
  --green:#3aaa3f;
  --green-dark:#2f9634;
  --teal:#0f4f5e;
  --ink:#222;
  --body:#555;
  --grey-bg:#ececec;
  --footer:#4a4a4a;
  --footer-text:#cfcfcf;
  --white:#fff;
}
*{box-sizing:border-box;margin:0;padding:0}
html,body{width:1200px;height:3291px;overflow:hidden}
body{font-family:"Open Sans",Arial,sans-serif;color:var(--body);background:var(--white);font-size:12px}
h1,h2,h3,h4,.nav,.btn,.brand{font-family:"Raleway",Arial,sans-serif}
.container{width:880px;margin:0 auto;position:relative}

/* header */
.site-header{height:79px;display:flex;align-items:center;justify-content:space-between;padding:0 160px}
.brand{display:flex;align-items:center;gap:10px;color:var(--green);font-size:17px;font-weight:500}
.brand-dot{width:30px;height:30px;border:2px solid var(--green);border-radius:50%}
.nav{display:flex;align-items:center;gap:30px;font-size:13px;font-weight:600;color:var(--ink)}
.nav .active{color:var(--green)}
.nav .login{background:var(--green);color:#fff;border-radius:16px;padding:7px 20px;font-size:12px}

/* hero */
.hero{position:relative;height:559px;background:radial-gradient(circle at 66% 12%,rgba(255,250,225,.75) 0,rgba(255,250,225,0) 22%),linear-gradient(180deg,#c9c7b8 0%,#8a8a6a 35%,#6f6a3a 65%,#3b3720 100%);display:flex;flex-direction:column;align-items:center;justify-content:center;text-align:center;color:#fff}
.hero h1{font-size:46px;font-weight:700;margin-bottom:16px;text-shadow:0 2px 6px rgba(0,0,0,.3)}
.hero p{font-family:"Raleway",sans-serif;font-size:20px;font-weight:700;letter-spacing:.5px}
.hero-arrow{position:absolute;top:250px;width:46px;height:60px;background:rgba(0,0,0,.15);display:flex;align-items:center;justify-content:center}
.hero-arrow.left{left:0}.hero-arrow.right{right:0}

/* welcome */
.welcome{height:496px;padding-top:38px}
.section-title{font-size:26px;font-weight:500;color:var(--ink);text-align:center}
.cards{display:flex;justify-content:space-between;margin-top:34px}
.card{width:277px}
.card-photo{height:171px}
.card h3{font-size:20px;font-weight:500;color:var(--ink);margin:24px 0 14px}
.card p{font-size:10.5px;line-height:1.7;margin-bottom:20px}
.btn{display:inline-block;font-size:10.5px;font-weight:700;text-transform:uppercase}
.btn-green{background:var(--green);color:#fff;padding:12px 20px}

/* premium */
.premium{height:483px;background:var(--grey-bg);padding-top:70px}
.premium-box{display:flex;height:336px;background:#fff}
.premium-text{width:440px;padding:46px 40px}
.premium-text h3{font-size:21px;font-weight:600;color:var(--ink);margin-bottom:18px}
.premium-text ul{list-style:none;margin-bottom:18px}
.premium-text li{font-size:11.5px;line-height:2;color:#444;padding-left:16px;position:relative}
.premium-text li::before{content:"";position:absolute;left:0;top:10px;width:7px;height:7px;border-radius:50%;background:var(--teal)}
.premium-video{flex:1;position:relative;background:linear-gradient(135deg,#8a5a4a,#394a6e 50%,#2a2a2a)}
.play{position:absolute;left:50%;top:50%;transform:translate(-50%,-50%);width:66px;height:44px;background:#1c1c1c;border-radius:4px;display:flex;align-items:center;justify-content:center}

/* story band */
.story{position:relative;height:391px;background:linear-gradient(180deg,#b9c3c7 0%,#667a4c 40%,#5b6a3a 70%,#6d5c3a 100%)}
.story-quote{position:absolute;left:582px;top:123px;width:458px;height:142px;background:var(--green);border-radius:14px;color:#fff;padding:18px 30px;text-align:center}
.story-quote h3{font-size:24px;font-weight:500;margin-bottom:14px}
.story-quote p{font-size:14px;line-height:1.7}

/* testimonials */
.testimonials{height:329px;padding-top:46px;text-align:center}
.testimonial{display:flex;align-items:flex-start;margin:30px auto 0;width:650px;text-align:center}
.t-badges{position:relative;width:110px;height:80px;flex:none;margin-top:8px}
.t-badge{position:absolute;left:0;top:0;width:74px;height:74px;border-radius:50%;background:var(--green)}
.t-avatar{position:absolute;left:38px;top:2px;width:70px;height:70px;border-radius:50%;background:#c9b9a8;border:3px solid #fff}
.t-body{flex:1;padding-left:20px}
.t-body blockquote{font-style:italic;font-size:11.5px;line-height:1.95;color:#444}
.t-body .mark{font-family:Georgia,serif;font-style:normal;font-weight:700;font-size:22px;line-height:0;color:#333;vertical-align:-6px}
.t-body cite{display:block;font-style:normal;font-family:"Raleway",sans-serif;font-size:15px;font-weight:600;color:#333;margin-top:16px}
.dots{display:flex;gap:4px;justify-content:center;margin-top:32px}
.dots span{width:13px;height:13px;border-radius:50%;background:var(--teal)}
.dots span:first-child{background:var(--green)}

/* aspiring */
.aspiring{height:401px;background:var(--green);color:#fff;text-align:center;padding-top:44px}
.aspiring h2{font-size:26px;font-weight:500}
.steps{display:flex;justify-content:space-between;width:860px;margin:40px auto 0;position:relative}
.step{width:220px}
.step-icon{width:150px;height:88px;margin:0 auto;border-radius:50%;background:radial-gradient(ellipse at center,rgba(255,255,255,.55) 0%,rgba(255,255,255,.25) 45%,rgba(255,255,255,0) 72%)}
.step h4{font-size:15px;font-weight:500;margin-top:18px}
.step p{font-size:15px;line-height:1.45;margin-top:4px;font-family:"Raleway",sans-serif}
.step .btn-outline{display:inline-block;margin-top:20px;border:1.5px solid #fff;border-radius:18px;padding:8px 26px;font-size:11px;font-family:"Raleway",sans-serif}
.step-arrow{position:absolute;top:38px}

/* contact */
.contact{height:250px;text-align:center;padding-top:50px}
.contact h2{font-size:21px;font-weight:600;color:var(--teal)}
.contact p{font-size:10.5px;line-height:1.8;color:#444;margin:14px auto 0;width:520px}
.contact-actions{display:flex;gap:12px;justify-content:center;margin-top:28px}
.pill{font-family:"Raleway",sans-serif;font-size:11.5px;font-weight:700;text-transform:uppercase;border-radius:22px;padding:13px 24px;border:2px solid var(--teal)}
.pill.solid{background:var(--teal);color:#fff}
.pill.ghost{color:var(--teal)}

/* footer */
.site-footer{height:303px;background:var(--footer);color:var(--footer-text);position:relative}
.footer-brand{position:absolute;left:160px;top:98px;color:#fff;font-size:16px}
.footer-brand .brand-dot{border-color:#fff}
.footer-col{position:absolute;top:42px}
.footer-col h4{font-size:12px;font-weight:700;color:#fff;margin-bottom:16px;letter-spacing:.5px}
.footer-col li{list-style:none;font-size:11px;line-height:1.9}
.footer-col .link{color:var(--green)}
.socials{display:flex;gap:6px;margin-top:18px}
.socials span{width:20px;height:20px;border:1px solid #ddd;border-radius:50%}
.copyright{position:absolute;left:0;right:0;bottom:22px;text-align:center;font-size:10px}
</style>
</head>
<body>

<header class="site-header">
  <div class="brand"><span class="brand-dot"></span>Meadowrun Acres</div>
  <nav class="nav">
    <span class="active">Home</span><span>Aspiring Farmers</span><span>Investors</span><span>Retiring Farmer</span><span>Blog</span><span>Pricing</span><span class="login">Login</span>
  </nav>
</header>

<section class="hero" role="img" aria-label="Sunlit pasture with cattle grazing and a rider on horseback">
  <h1>Farm Ownership</h1>
  <p>IT'S TIME TO REALISE YOUR FARMING DREAM.</p>
  <span class="hero-arrow left"><svg width="14" height="26" viewBox="0 0 14 26"><path d="M12 2 2 13l10 11" fill="none" stroke="#fff" stroke-width="2"/></svg></span>
  <span class="hero-arrow right"><svg width="14" height="26" viewBox="0 0 14 26"><path d="M2 2l10 11L2 24" fill="none" stroke="#fff" stroke-width="2"/></svg></span>
</section>

<section class="welcome">
  <div class="container">
    <h2 class="section-title">Welcome to Meadowrun Acres</h2>
    <div class="cards">
      <article class="card">
        <div class="card-photo" role="img" aria-label="Open hay shed in a dry paddock" style="background:linear-gradient(180deg,#9fb4c4,#6d6448 55%,#4a4128)"></div>
        <h3>Farmers</h3>
        <p>Cras mattis consectetur purus sit amet fermentum bileo risus, porta ac consectetur ac, vestibulumlor te cenas faucibus mollis interdumatts.</p>
        <span class="btn btn-green">Read more</span>
      </article>
      <article class="card">
        <div class="card-photo" role="img" aria-label="People working rows of crops below green hills" style="background:linear-gradient(180deg,#5d8fd6,#9fc0e6 40%,#587a3c 60%,#3f5a2a)"></div>
        <h3>Investors</h3>
        <p>Cras mattis consectetur purus sit amet fermentum bileo risus, porta ac consectetur ac, vestibulumlor te cenas faucibus mollis interdumatts.</p>
        <span class="btn btn-green">Read more</span>
      </article>
      <article class="card">
        <div class="card-photo" role="img" aria-label="Farming family sitting together outdoors" style="background:linear-gradient(135deg,#a7a39a,#8a5048 50%,#5a6a7a)"></div>
        <h3>Retiring Farmers</h3>
        <p>Cras mattis consectetur purus sit amet fermentum bileo risus, porta ac consectetur ac, vestibulumlor te cenas faucibus mollis interdumatts.</p>
        <span class="btn btn-green">Read more</span>
      </article>
    </div>
  </div>
</section>

<section class="premium">
  <div class="container premium-box">
    <div class="premium-text">
      <h3>Premium Farmer to Receive</h3>
      <ul>
        <li>Free Fieldmark market analysis membership (valued at $300 pa)</li>
        <li>Farm business webinars (valued at $200)</li>
        <li>Corporate Partner Opportunities</li>
        <li>Public or Private profile (as required)</li>
        <li>Eligible to enter competitions and win prizes</li>
        <li>...and more. Visit our pricing page to find out more</li>
      </ul>
      <span class="btn btn-green">Join now</span>
    </div>
    <div class="premium-video" role="img" aria-label="Video still of a young farmer beside farm machinery">
      <span class="play"><svg width="16" height="18" viewBox="0 0 16 18"><path d="M2 1l13 8-13 8z" fill="#fff"/></svg></span>
    </div>
  </div>
</section>

<section class="story" role="img" aria-label="Family walking with cattle and a rider on horseback in bushland">
  <div class="story-quote">
    <h3>Tom &amp; Ellie Harlan</h3>
    <p>I really love to farm as farming is forever . I would love to farm anywhere there is an opportunity to live and work in a local farming community.</p>
  </div>
</section>

<section class="testimonials">
  <h2 class="section-title">Testimonials</h2>
  <div class="testimonial">
    <div class="t-badges"><span class="t-badge"></span><span class="t-avatar" role="img" aria-label="Portrait of the reviewer"></span></div>
    <div class="t-body">
      <blockquote><span class="mark">&#8220;</span> Meadowrun Acres can offer an opportunity to put people with the skills and ambition, with either a farming family looking to transition into retirement or for someone who doesn't have the skills but has capital and wants somewhere safe to invest Farms could have the ability to get more young people into small rural areas. We both love rural Australia and think <span class="mark">&#8221;</span></blockquote>
      <cite>Neil Arden, aspiring farmer, Dunmore Plains</cite>
    </div>
  </div>
  <div class="dots"><span></span><span></span><span></span></div>
</section>

<section class="aspiring">
  <h2>Aspiring Farmers</h2>
  <div class="steps">
    <svg class="step-arrow" style="left:190px" width="170" height="12" viewBox="0 0 170 12"><path d="M0 6h164m-6-5 6 5-6 5" fill="none" stroke="#fff" stroke-width="1.3" opacity=".8"/></svg>
    <svg class="step-arrow" style="left:500px" width="170" height="12" viewBox="0 0 170 12"><path d="M0 6h164m-6-5 6 5-6 5" fill="none" stroke="#fff" stroke-width="1.3" opacity=".8"/></svg>
    <div class="step">
      <div class="step-icon" role="img" aria-label="Farmer with pitchfork illustration"></div>
      <h4>Step 1</h4>
      <p>Register as an Aspiring Farmer</p>
      <span class="btn-outline">Register</span>
    </div>
    <div class="step">
      <div class="step-icon" role="img" aria-label="Tractor illustration"></div>
      <h4>Step 2</h4>
      <p>Build your farm skills to get yourself farm-ready.</p>
      <span class="btn-outline">Farm-Ready</span>
    </div>
    <div class="step">
      <div class="step-icon" role="img" aria-label="Farmhouse and tree illustration"></div>
      <h4>Step 3</h4>
      <p>Together we find you your dream farm.</p>
      <span class="btn-outline">Match- Making</span>
    </div>
  </div>
</section>

<section class="contact">
  <h2>Get in touch discuss the best farm succession opportunity for you</h2>
  <p>Cras mattis consectetur purus sit amet fermentum bileo risus, porta ac consectetur ac, vestibulumlor tur purus sit amet fermentum bileo risus, porta ac consectetur ac, vestibulumlor.</p>
  <div class="contact-actions"><span class="pill solid">Enquire now</span><span class="pill ghost">Find out more</span></div>
</section>

<footer class="site-footer">
  <div class="brand footer-brand"><span class="brand-dot"></span>Meadowrun Acres</div>
  <div class="footer-col" style="left:400px"><h4>SITE MAP</h4><ul><li>Farmers</li><li>Investors</li><li>Retiring</li><li>About</li><li>Pricing</li></ul></div>
  <div class="footer-col" style="left:540px"><h4>SUPPORT</h4><ul><li>Contact</li><li>Terms of Service</li><li>Privacy</li><li>Newsletter</li><li>Donate</li></ul></div>
  <div class="footer-col" style="left:691px"><h4>LINKS</h4><ul><li>Home</li><li>Aspiring Farmers</li><li>Investors</li><li>Retiring Farmer</li><li>Blog</li><li>Pricing</li></ul></div>
  <div class="footer-col" style="left:849px"><h4>GET IN TOUCH</h4><ul><li>Call us at +00 555 014 2290</li><li>Mail us at support@meadowrunacres.example</li><li>Chat with us <span class="link">here</span></li></ul>
    <div class="socials"><span></span><span></span><span></span><span></span><span></span></div>
  </div>
  <p class="copyright">Copyright &copy; 2017 Meadowrun Acres. All Copyrights reserved</p>
</footer>

</body>
</html>
```